Melorix artwork for new single release

I need Melorix artwork creating to release a new single on there.

The specs are:

Ideal size: 3000 x 3000 pixels
Minimum size: 1400 x 1400 pixels
Aspect ratio: 1:1 (must be a perfect square)
File format: JPG or PNG
Color space: sRGB
File size: Max 4MB

The song is called "Was It Ever Rain?"
The artist is "Martin Hollow"

We have no images of Martin, so it really is open to imagination.

Target Market(s)

Melorix listeners

Industry/Entity Type

Music

```html
<!DOCTYPE html>
<html lang="en">
<head>
<meta charset="utf-8">
<title>Was It Ever Rain? — Martin Hollow</title>
<link rel="stylesheet" href="https://fonts.googleapis.com/css2?family=DM+Sans:wght@700&display=swap">
<style>
  :root {
    --sky-blue: #4a5fd6;
    --violet: #7a2fb8;
    --magenta: #e0179a;
    --hot-pink: #ff3fa6;
    --plum: #5a1a6e;
    --white: #ffffff;
  }
  html, body {
    margin: 0;
    padding: 0;
    width: 1200px;
    height: 1200px;
    overflow: hidden;
    background: var(--plum);
  }
  .cover {
    position: relative;
    width: 1200px;
    height: 1200px;
    overflow: hidden;
  }
  .cover__backdrop {
    position: absolute;
    inset: 0;
    background:
      radial-gradient(ellipse 38% 30% at 55% 62%, rgba(255, 90, 120, 0.75), transparent 70%),
      radial-gradient(ellipse 30% 45% at 8% 55%, rgba(90, 26, 110, 0.7), transparent 70%),
      radial-gradient(ellipse 28% 45% at 94% 45%, rgba(70, 40, 150, 0.65), transparent 70%),
      radial-gradient(ellipse 60% 20% at 50% 24%, rgba(90, 30, 100, 0.6), transparent 75%),
      linear-gradient(180deg,
        var(--sky-blue) 0%,
        var(--violet) 14%,
        var(--magenta) 34%,
        var(--hot-pink) 58%,
        var(--magenta) 80%,
        #c81c8e 100%);
  }
  .cover__title {
    position: absolute;
    left: 0;
    right: 0;
    top: 215px;
    margin: 0;
    text-align: center;
    font-family: "DM Sans", sans-serif;
    font-weight: 700;
    color: var(--white);
    line-height: 0.98;
    letter-spacing: -2px;
  }
  .cover__title-line {
    display: block;
  }
  .cover__title-line--small {
    font-size: 120px;
  }
  .cover__title-line--large {
    font-size: 195px;
  }
  .cover__artist {
    position: absolute;
    left: 0;
    right: 0;
    top: 1078px;
    margin: 0;
    text-align: center;
    font-family: "DM Sans", sans-serif;
    font-weight: 700;
    font-size: 50px;
    line-height: 1.2;
    letter-spacing: 0.5px;
    color: var(--white);
  }
</style>
</head>
<body>
  <main class="cover">
    <div class="cover__backdrop" role="img" aria-label="Dreamy photograph of a figure in a light dress walking through a tall-grass field, washed in magenta, pink and violet light leaks"></div>
    <h1 class="cover__title">
      <span class="cover__title-line cover__title-line--small">Was</span>
      <span class="cover__title-line cover__title-line--large">It</span>
      <span class="cover__title-line cover__title-line--large">Ever</span>
      <span class="cover__title-line cover__title-line--large">Rain?</span>
    </h1>
    <p class="cover__artist">Martin Hollow</p>
  </main>
</body>
</html>
```